Triveld Business Card Design

We need a modern great looking premium business card design that can be customized by person that also displays a contact QR code. It should match our existing branding and website Triveld.com . We need to be able to upload it to plip for continued customization and use across a good size company.

```html
<!DOCTYPE html>
<html lang="en">
<head>
<meta charset="utf-8">
<title>Triveld Business Card</title>
<link rel="stylesheet" href="https://fonts.googleapis.com/css2?family=Josefin+Sans:wght@400;600;700&display=swap">
<style>
  :root {
    --navy: #1b1e33;
    --brand-blue: #1a6db5;
    --paper: #ffffff;
    --paper-shade: #ebecee;
    --ink: #1f2230;
    --rule: #6c6f78;
    --faint: #dde7ef;
    --backdrop: #d9dadc;
  }
  * { margin: 0; padding: 0; box-sizing: border-box; }
  html, body { width: 1200px; height: 900px; overflow: hidden; }
  body {
    background: var(--backdrop);
    font-family: "Josefin Sans", sans-serif;
    color: var(--ink);
    position: relative;
  }
  .card {
    position: absolute;
    left: 250px;
    width: 700px;
    height: 400px;
    border-radius: 30px;
    overflow: hidden;
    background: linear-gradient(110deg, var(--paper-shade) 0%, var(--paper) 70%);
    box-shadow: 0 10px 28px rgba(0,0,0,0.18);
  }
  .card-front { top: 35px; }
  .card-back { top: 465px; }
  .band { position: absolute; inset: 0; width: 100%; height: 100%; }
  .brand {
    position: absolute;
    display: flex;
    align-items: center;
    gap: 16px;
    color: var(--brand-blue);
    font-weight: 700;
    letter-spacing: 1px;
  }
  .brand-mark {
    display: block;
    background: var(--brand-blue);
  }
  .card-front .brand { top: 110px; left: 0; right: 0; justify-content: center; font-size: 70px; }
  .card-front .brand-mark { width: 44px; height: 44px; }
  .front-url {
    position: absolute;
    left: 42px;
    bottom: 42px;
    color: var(--paper);
    font-size: 17px;
    letter-spacing: 4px;
  }
  .card-back .brand { top: 92px; left: 40px; font-size: 58px; }
  .card-back .brand-mark { width: 36px; height: 36px; }
  .back-decor {
    position: absolute;
    top: 0;
    right: 0;
    width: 250px;
    height: 190px;
    background: var(--faint);
    opacity: 0.7;
  }
  .divider {
    position: absolute;
    left: 104px;
    right: 30px;
    top: 238px;
    height: 1px;
    background: var(--rule);
  }
  .person { position: absolute; left: 48px; top: 190px; }
  .person-name {
    color: var(--brand-blue);
    font-weight: 700;
    font-size: 24px;
    letter-spacing: 0.5px;
    text-transform: uppercase;
  }
  .person-role { font-size: 20px; margin-top: 2px; }
  .contact-list {
    position: absolute;
    left: 48px;
    top: 262px;
    list-style: none;
    font-size: 17px;
  }
  .contact-list li { display: flex; align-items: center; gap: 12px; height: 26px; }
  .contact-list svg { width: 16px; height: 16px; fill: var(--brand-blue); }
  .address {
    position: absolute;
    left: 456px;
    top: 318px;
    color: var(--paper);
    font-size: 16px;
    line-height: 26px;
    white-space: nowrap;
  }
</style>
</head>
<body>

<section class="card card-front" aria-label="Card front">
  <svg class="band" viewBox="0 0 700 400" preserveAspectRatio="none" aria-hidden="true">
    <path d="M0 290 H300 C330 290 335 332 370 332 H700 V400 H0 Z" fill="var(--navy)"/>
  </svg>
  <div class="brand"><span class="brand-mark"></span>Triveld</div>
  <p class="front-url">www.triveld.com</p>
</section>

<section class="card card-back" aria-label="Card back">
  <svg class="band" viewBox="0 0 700 400" preserveAspectRatio="none" aria-hidden="true">
    <path d="M0 374 H390 C415 374 410 298 442 298 H700 V400 H0 Z" fill="var(--navy)"/>
  </svg>
  <div class="back-decor" aria-hidden="true"></div>
  <div class="brand"><span class="brand-mark"></span>Triveld</div>
  <div class="divider"></div>
  <div class="person">
    <p class="person-name">Dana Whitfield</p>
    <p class="person-role">CEO</p>
  </div>
  <ul class="contact-list">
    <li>
      <svg viewBox="0 0 16 16" aria-hidden="true"><path d="M3.5 1 L6 1 L7 4.5 L5.4 5.8 C6.3 7.8 8.2 9.7 10.2 10.6 L11.5 9 L15 10 L15 12.5 C15 13.9 13.9 15 12.5 15 C6.7 15 1 9.3 1 3.5 C1 2.1 2.1 1 3.5 1Z"/></svg>
      (800) 555-0142
    </li>
    <li>
      <svg viewBox="0 0 16 16" aria-hidden="true"><path d="M8 1a7 7 0 1 0 0 14A7 7 0 0 0 8 1Zm0 1.4c.8.8 1.5 2.2 1.8 3.8H6.2C6.5 4.6 7.2 3.2 8 2.4ZM2.5 7.4h2.4c0 .4-.1.8-.1 1.2h-2.3a5.6 5.6 0 0 1 0-1.2Zm.3 2.4h2.1c.2 1.3.6 2.4 1.2 3.3a5.6 5.6 0 0 1-3.3-3.3Zm2.1-3.6H2.8a5.6 5.6 0 0 1 3.3-3.3c-.6.9-1 2-1.2 3.3ZM8 13.6c-.8-.8-1.5-2.2-1.8-3.8h3.6c-.3 1.6-1 3-1.8 3.8Zm2-5H6c0-.4 0-.8.1-1.2h3.8c.1.4.1.8.1 1.2Zm0 4.5c.6-.9 1-2 1.2-3.3h2.1a5.6 5.6 0 0 1-3.3 3.3Zm1.2-4.5c0-.4 0-.8-.1-1.2h2.4a5.6 5.6 0 0 1 0 1.2H11.2Zm0-2.4C11 4.9 10.6 3.8 10 2.9a5.6 5.6 0 0 1 3.3 3.3h-2.1Z"/></svg>
      www.triveld.com
    </li>
    <li>
      <svg viewBox="0 0 16 16" aria-hidden="true"><path d="M1 3h14v1.2L8 9 1 4.2Zm0 2.6 7 4.8 7-4.8V13H1Z"/></svg>
      support@triveld.com
    </li>
    <li>
      <svg viewBox="0 0 16 16" aria-hidden="true"><path d="M1 3h14v1.2L8 9 1 4.2Zm0 2.6 7 4.8 7-4.8V13H1Z"/></svg>
      sales@triveld.com
    </li>
  </ul>
  <p class="address">Attn: KLM, 240 E Cedar Ave<br>Riverton, OK 73015</p>
</section>

</body>
</html>
```